New Company Business Card design

Looking for a corporate looking business card utilising my new logo design - the logo i would like embossed as one option and flat as another - simplistic but stylish - less is more - we are an import export business launching into the market - i would like a couple of options as main background - Grey or Black

```html
<!DOCTYPE html>
<html lang="en">
<head>
<meta charset="utf-8">
<title>Meridian Trade Partners – Business Card</title>
<link href="https://fonts.googleapis.com/css2?family=Roboto:wght@400;500&family=Roboto+Condensed:wght@500&display=swap" rel="stylesheet">
<style>
  :root {
    --backdrop: #a98260;
    --card-white: #f5f5f5;
    --card-grey: #6b6c70;
    --band-grey: #6b6c70;
    --brand-blue: #1a75bb;
    --text-grey: #4d4e52;
    --white: #ffffff;
  }
  * { margin: 0; padding: 0; box-sizing: border-box; }
  html, body { width: 1200px; height: 960px; overflow: hidden; }
  body {
    background: var(--backdrop);
    position: relative;
    font-family: "Roboto", Arial, sans-serif;
  }
  .card {
    position: absolute;
    width: 600px;
    height: 343px;
    box-shadow: 0 3px 8px rgba(0,0,0,0.35);
  }
  .card-front {
    left: 314px; top: 113px;
    background: var(--card-white);
    border-top: 16px solid var(--band-grey);
    border-bottom: 16px solid var(--brand-blue);
  }
  .card-back {
    left: 311px; top: 472px;
    background: var(--card-grey);
  }
  .brand-lockup {
    position: absolute;
    left: 60px; top: 115px;
    width: 270px;
    display: flex;
    align-items: center;
    justify-content: center;
    gap: 10px;
    color: var(--brand-blue);
    font-weight: 500;
    font-size: 19px;
    letter-spacing: 0.5px;
    text-transform: uppercase;
    line-height: 1.15;
  }
  .brand-dot {
    width: 34px; height: 34px;
    border-radius: 50%;
    background: var(--brand-blue);
    flex: none;
  }
  .contact-block {
    position: absolute;
    left: 356px; top: 71px;
    color: var(--text-grey);
  }
  .person-name {
    font-family: "Roboto Condensed", Arial, sans-serif;
    font-weight: 500;
    font-size: 24px;
    color: var(--brand-blue);
    line-height: 1;
  }
  .person-role {
    font-size: 15px;
    margin-top: 5px;
    text-transform: uppercase;
  }
  .address {
    font-size: 14px;
    line-height: 19px;
    margin-top: 12px;
  }
  .contact-list {
    list-style: none;
    margin-top: 10px;
    font-size: 14px;
  }
  .contact-list li {
    display: flex;
    align-items: center;
    gap: 9px;
    height: 19px;
  }
  .contact-list svg { width: 13px; height: 13px; fill: var(--brand-blue); flex: none; }
  .back-lockup {
    position: absolute;
    left: 0; right: 0; top: 128px;
    display: flex;
    align-items: center;
    justify-content: center;
    gap: 16px;
    color: var(--white);
    font-weight: 500;
    font-size: 40px;
    letter-spacing: 2px;
    text-transform: uppercase;
  }
  .back-dot {
    width: 56px; height: 56px;
    border-radius: 50%;
    background: var(--white);
  }
  .back-url {
    position: absolute;
    left: 0; right: 0; top: 288px;
    text-align: center;
    color: var(--white);
    font-size: 14px;
    letter-spacing: 1.6px;
  }
</style>
</head>
<body>
  <section class="card card-front">
    <div class="brand-lockup">
      <span class="brand-dot"></span>
      <span>Meridian Trade<br>Partners</span>
    </div>
    <div class="contact-block">
      <p class="person-name">DANIEL HART</p>
      <p class="person-role">CEO/Founder</p>
      <p class="address">2140 Harbor View Road<br>Kodiak, Alaska 99615</p>
      <ul class="contact-list">
        <li><svg viewBox="0 0 16 16"><path d="M3.5 1l3 3-1.8 1.8c.9 2 2.5 3.6 4.5 4.5L11 8.5l3 3-2 2.5C6.5 13.5 2.5 9.5 1 3.5z"/></svg>555 201 4471</li>
        <li><svg viewBox="0 0 16 16"><path d="M4 0h8a1 1 0 0 1 1 1v14a1 1 0 0 1-1 1H4a1 1 0 0 1-1-1V1a1 1 0 0 1 1-1zm1 2v10h6V2zm3 11a1 1 0 1 0 0 2 1 1 0 0 0 0-2z"/></svg>555 318 6620</li>
        <li><svg viewBox="0 0 16 16"><path d="M4 1h8v4H4zM1 6h14v7h-3v2H4v-2H1zm4 4v4h6v-4z"/></svg>555 742 0983</li>
        <li><svg viewBox="0 0 16 16"><path d="M1 3h14v10H1zm1.5 1.2L8 8.5l5.5-4.3z"/></svg>daniel@meridiantrade.example</li>
        <li><svg viewBox="0 0 16 16"><path d="M8 0a8 8 0 1 0 0 16A8 8 0 0 0 8 0zm-1 2.5c-1 1.5-.5 2.5.5 3s1 2-.5 2.5S5 10 6 12c-2-.5-3.5-2.5-3.5-4.5C2.5 5 4.5 3 7 2.5zm3 2c1.5.5 2 2 1.5 3s-2 .5-2.5-.5.5-2 1-2.5z"/></svg>www.meridiantrade.example</li>
      </ul>
    </div>
  </section>

  <section class="card card-back">
    <div class="back-lockup">
      <span class="back-dot"></span>
      <span>Meridian</span>
    </div>
    <p class="back-url">www.meridiantradepartners.example</p>
  </section>
</body>
</html>
```